Bright Towns Forum PowerPoint Design Template and Sample Deck

The Bright Towns Forum is an international organization that seeks to improve the livability, workability and sustainability of the world’s cities.
We seek a versatile PowerPoint design template with 10 slide types plus a “self-documenting” sample deck. Your design will be used in keynote speeches and workshops around the world.
After the contest is completed, we will ask the winning designer to add 10-20 additional slide types for $75 per slide. We also seek a long-term relationship whereby we can request “custom” slides and/or ask the designer to touch up the slides we build to make them better.
FILES. We have uploaded several files:
2. PALETTE. Shows our official colors.
3 LOGOS. Several individual files with different variations of our logo. Some with our motto, some without.
2. SAMPLE SLIDES. Because we were unable to successfully upload our sample deck, we are making it available via this FileNook link:
https://www.filenook-example.com/s/k7qrtmzp2wd9hxa/The%20Bright%20Towns%20Forum%20Design%20Contest%20Notes.docx?dl=0
Target Market(s)
Mayors, department heads, CIOs, senior executives from technology companies
Industry/Entity Type
Information Technology
Colors
Designer to choose colors to be used in the design.
Requirements
Must have
- Please see uploaded Word document for requirements, nice to haves and should not haves and uploaded palette for color preferences.
Nice to have
- see above
Should not have
- see above

```html
<!DOCTYPE html>
<html lang="en">
<head>
<meta charset="utf-8">
<title>Individual Slides 01e – Bright Towns Forum</title>
<link href="https://fonts.googleapis.com/css2?family=Roboto:wght@900&family=Roboto+Condensed:wght@300&family=Open+Sans:ital,wght@0,400;0,600;0,700;1,400&display=swap" rel="stylesheet">
<style>
  :root{
    --pink:#e2b9bc;
    --navy:#0e2b5c;
    --cover:#0c4690;
    --title:#1f5fbf;
    --blue:#1a4f9c;
    --dark:#0b3a7e;
    --sky:#6d98d4;
    --orange:#ef8a22;
    --red:#e84a2c;
    --gray:#7a7a7a;
    --lgray:#aaaaaa;
    --green:#7aa02c;
    --yellow:#f6b91a;
    --paper:#f7f7f7;
    --wood-a:#a38b66;
    --wood-b:#8b7452;
  }
  html,body{margin:0;padding:0;width:1200px;height:1200px;overflow:hidden;background:#fff}
  .canvas{position:relative;width:1200px;height:1200px}
  .heading{position:absolute;top:52px;left:0;width:1200px;text-align:center;margin:0;
    font:900 70px/1 'Roboto',sans-serif;color:var(--pink);letter-spacing:1px}
  .subheading{position:absolute;top:144px;left:0;width:1200px;text-align:center;margin:0;
    font:300 29px/1 'Roboto Condensed',sans-serif;color:var(--pink)}
  .backdrop{position:absolute;top:282px;left:0;width:1200px;height:675px;
    background:linear-gradient(100deg,var(--wood-a),var(--wood-b) 45%,var(--wood-a) 70%,var(--wood-b))}
  .slide{position:absolute;width:320px;height:181px;box-shadow:0 4px 8px rgba(0,0,0,.35);background:var(--paper)}
  .c1{left:71px}.c2{left:446px}.c3{left:820px}
  .r1{top:314px}.r2{top:520px}.r3{top:731px}
  .t-title{font:700 14px 'Open Sans',sans-serif;fill:var(--title)}
  .t-body{font:italic 4.2px 'Open Sans',sans-serif;fill:#8a8a8a}
  .t-label{font:600 4.4px 'Open Sans',sans-serif;fill:#444}
  .t-cap{font:3.4px 'Open Sans',sans-serif;fill:#9a9a9a}
  .t-in{font:700 3.6px 'Open Sans',sans-serif;fill:#fff}
  .t-brand{font:400 10px 'Open Sans',sans-serif;fill:#fff}
  .t-foot{font:3.4px 'Open Sans',sans-serif;fill:#d6def0}
  .t-num{font:700 3.4px 'Open Sans',sans-serif;fill:#fff}
  .t-cover{font:700 10px 'Open Sans',sans-serif;fill:#fff}
  .t-cover-sub{font:italic 6px 'Open Sans',sans-serif;fill:#dfe8f7}
  .glyph{fill:none;stroke:#fff;stroke-width:1.2}
</style>
</head>
<body>
<div class="canvas">
  <h1 class="heading">INDIVIDUAL SLIDES - 01e</h1>
  <p class="subheading">(Bigger size for more details)</p>
  <div class="backdrop" role="img" aria-label="Warm brown wood grain tabletop backdrop"></div>

  <!-- Cover slide -->
  <svg class="slide c1 r1" viewBox="0 0 400 226">
    <rect width="400" height="226" fill="var(--cover)"/>
    <g fill="#ffffff" opacity=".05">
      <polygon points="20,30 120,0 160,110 60,140"/>
      <polygon points="80,120 170,90 200,190 110,226 70,226"/>
    </g>
    <text class="t-cover" x="348" y="116" text-anchor="end">10 Linear Progress</text>
    <text class="t-cover-sub" x="348" y="128" text-anchor="end">Slide Ideas...</text>
    <circle cx="364" cy="112" r="6" fill="none" stroke="#fff" stroke-width="1"/>
    <polygon points="362,109 362,115 367,112" fill="#fff"/>
  </svg>

  <!-- Slide 49: icon grid -->
  <svg class="slide c2 r1" viewBox="0 0 400 226">
    <text class="t-title" x="200" y="20" text-anchor="middle">Your Slide Title</text>
    <g fill="var(--title)"><rect x="191" y="30" width="2" height="2"/><rect x="195" y="30" width="2" height="2"/><rect x="199" y="30" width="2" height="2"/><rect x="203" y="30" width="2" height="2"/><rect x="207" y="30" width="2" height="2"/></g>
    <text class="t-body" x="30" y="51">Short summary line for this slide. Replace with your own opening sentence here.</text>
    <text class="t-body" x="30" y="60">Keep it brief so the visual can carry the message.</text>
    <g>
      <circle cx="72" cy="91" r="13" fill="var(--dark)"/><circle cx="157" cy="91" r="13" fill="var(--blue)"/><circle cx="242" cy="91" r="13" fill="var(--sky)"/><circle cx="327" cy="91" r="13" fill="var(--green)"/>
      <circle cx="72" cy="155" r="13" fill="var(--orange)"/><circle cx="157" cy="155" r="13" fill="var(--gray)"/><circle cx="242" cy="155" r="13" fill="var(--green)"/><circle cx="327" cy="155" r="13" fill="var(--lgray)"/>
      <g class="glyph"><rect x="67" y="86" width="10" height="10" rx="1"/><rect x="152" y="86" width="10" height="10" rx="1"/><rect x="237" y="86" width="10" height="10" rx="1"/><rect x="322" y="86" width="10" height="10" rx="1"/><rect x="67" y="150" width="10" height="10" rx="1"/><rect x="152" y="150" width="10" height="10" rx="1"/><rect x="237" y="150" width="10" height="10" rx="1"/><rect x="322" y="150" width="10" height="10" rx="1"/></g>
    </g>
    <g text-anchor="middle">
      <text class="t-label" x="72" y="117">Your Title Here</text><text class="t-cap" x="72" y="123">Short note for this item.</text>
      <text class="t-label" x="157" y="117">Your Title Here</text><text class="t-cap" x="157" y="123">Short note for this item.</text>
      <text class="t-label" x="242" y="117">Your Title Here</text><text class="t-cap" x="242" y="123">Short note for this item.</text>
      <text class="t-label" x="327" y="117">Your Title Here</text><text class="t-cap" x="327" y="123">Short note for this item.</text>
      <text class="t-label" x="72" y="181">Your Title Here</text><text class="t-cap" x="72" y="187">Short note for this item.</text>
      <text class="t-label" x="157" y="181">Your Title Here</text><text class="t-cap" x="157" y="187">Short note for this item.</text>
      <text class="t-label" x="242" y="181">Your Title Here</text><text class="t-cap" x="242" y="187">Short note for this item.</text>
      <text class="t-label" x="327" y="181">Your Title Here</text><text class="t-cap" x="327" y="187">Short note for this item.</text>
    </g>
    <rect y="203" width="400" height="23" fill="var(--navy)"/>
    <text class="t-brand" x="14" y="218">Bright Towns Forum</text>
    <text class="t-foot" x="360" y="216" text-anchor="end">Bright Towns Forum | Copyright 2017</text>
    <circle cx="371" cy="214" r="5" fill="var(--title)"/><text class="t-num" x="371" y="215.3" text-anchor="middle">49</text>
  </svg>

  <!-- Slide 50: four banners -->
  <svg class="slide c3 r1" viewBox="0 0 400 226">
    <text class="t-title" x="200" y="20" text-anchor="middle">Your Slide Title</text>
    <g fill="var(--title)"><rect x="191" y="30" width="2" height="2"/><rect x="195" y="30" width="2" height="2"/><rect x="199" y="30" width="2" height="2"/><rect x="203" y="30" width="2" height="2"/><rect x="207" y="30" width="2" height="2"/></g>
    <text class="t-body" x="30" y="51">Short summary line for this slide. Replace with your own opening sentence here.</text>
    <text class="t-body" x="30" y="60">Keep it brief so the visual can carry the message.</text>
    <rect x="40" y="75" width="63" height="70" fill="var(--blue)"/><polygon points="66,145 77,145 71.5,151" fill="var(--blue)"/>
    <rect x="126" y="75" width="63" height="70" fill="var(--orange)"/><polygon points="152,145 163,145 157.5,151" fill="var(--orange)"/>
    <rect x="212" y="75" width="63" height="70" fill="var(--gray)"/><polygon points="238,145 249,145 243.5,151" fill="var(--gray)"/>
    <rect x="297" y="75" width="63" height="70" fill="var(--red)"/><polygon points="323,145 334,145 328.5,151" fill="var(--red)"/>
    <g class="glyph"><circle cx="71.5" cy="99" r="5"/><circle cx="157.5" cy="99" r="5"/><circle cx="243.5" cy="99" r="5"/><circle cx="328.5" cy="99" r="5"/></g>
    <g text-anchor="middle">
      <text class="t-in" x="71.5" y="121">FUTURE</text>
      <text class="t-in" x="157.5" y="121">LEADERSHIP</text>
      <text class="t-in" x="243.5" y="121">TEAMING</text>
      <text class="t-in" x="328.5" y="119">SKILL</text><text class="t-in" x="328.5" y="124">BUILDING</text>
      <text class="t-label" x="71.5" y="168">Your Title Here</text><text class="t-cap" x="71.5" y="174">Short note for this item.</text>
      <text class="t-label" x="157.5" y="168">Your Title Here</text><text class="t-cap" x="157.5" y="174">Short note for this item.</text>
      <text class="t-label" x="243.5" y="168">Your Title Here</text><text class="t-cap" x="243.5" y="174">Short note for this item.</text>
      <text class="t-label" x="328.5" y="168">Your Title Here</text><text class="t-cap" x="328.5" y="174">Short note for this item.</text>
    </g>
    <rect y="203" width="400" height="23" fill="var(--navy)"/>
    <text class="t-brand" x="14" y="218">Bright Towns Forum</text>
    <text class="t-foot" x="360" y="216" text-anchor="end">Bright Towns Forum | Copyright 2017</text>
    <circle cx="371" cy="214" r="5" fill="var(--title)"/><text class="t-num" x="371" y="215.3" text-anchor="middle">50</text>
  </svg>

  <!-- Slide 51: overlapping circles -->
  <svg class="slide c1 r2" viewBox="0 0 400 226">
    <text class="t-title" x="200" y="20" text-anchor="middle">Your Slide Title</text>
    <g fill="var(--title)"><rect x="191" y="30" width="2" height="2"/><rect x="195" y="30" width="2" height="2"/><rect x="199" y="30" width="2" height="2"/><rect x="203" y="30" width="2" height="2"/><rect x="207" y="30" width="2" height="2"/></g>
    <text class="t-body" x="30" y="51">Short summary line for this slide. Replace with your own opening sentence here.</text>
    <text class="t-body" x="30" y="60">Keep it brief so the visual can carry the message.</text>
    <circle cx="320" cy="114" r="32" fill="var(--lgray)"/>
    <circle cx="262" cy="114" r="32" fill="var(--green)"/>
    <circle cx="204" cy="114" r="32" fill="var(--gray)"/>
    <circle cx="146" cy="114" r="32" fill="var(--red)"/>
    <circle cx="88" cy="114" r="32" fill="var(--dark)"/>
    <g class="glyph"><rect x="82" y="108" width="12" height="12" rx="1"/><rect x="140" y="108" width="12" height="12" rx="1"/><rect x="198" y="108" width="12" height="12" rx="1"/><path d="M262 106 l6 2 v5 c0 4-3 6-6 7 c-3-1-6-3-6-7 v-5z"/><rect x="314" y="108" width="12" height="12" rx="1"/></g>
    <g fill="#ccc"><circle cx="88" cy="158" r="1"/><circle cx="146" cy="158" r="1"/><circle cx="204" cy="158" r="1"/><circle cx="262" cy="158" r="1"/><circle cx="320" cy="158" r="1"/></g>
    <g text-anchor="middle">
      <text class="t-label" x="88" y="174">Your Title Here</text><text class="t-cap" x="88" y="180">Short note for this item.</text>
      <text class="t-label" x="146" y="174">Your Title Here</text><text class="t-cap" x="146" y="180">Short note for this item.</text>
      <text class="t-label" x="204" y="174">Your Title Here</text><text class="t-cap" x="204" y="180">Short note for this item.</text>
      <text class="t-label" x="262" y="174">Your Title Here</text><text class="t-cap" x="262" y="180">Short note for this item.</text>
      <text class="t-label" x="320" y="174">Your Title Here</text><text class="t-cap" x="320" y="180">Short note for this item.</text>
    </g>
    <rect y="203" width="400" height="23" fill="var(--navy)"/>
    <text class="t-brand" x="14" y="218">Bright Towns Forum</text>
    <text class="t-foot" x="360" y="216" text-anchor="end">Bright Towns Forum | Copyright 2017</text>
    <circle cx="371" cy="214" r="5" fill="var(--title)"/><text class="t-num" x="371" y="215.3" text-anchor="middle">51</text>
  </svg>

  <!-- Slide 52: competition cluster -->
  <svg class="slide c2 r2" viewBox="0 0 400 226">
    <text class="t-title" x="200" y="20" text-anchor="middle">Your Slide Title</text>
    <g fill="var(--title)"><rect x="191" y="30" width="2" height="2"/><rect x="195" y="30" width="2" height="2"/><rect x="199" y="30" width="2" height="2"/><rect x="203" y="30" width="2" height="2"/><rect x="207" y="30" width="2" height="2"/></g>
    <text class="t-body" x="30" y="51">Short summary line for this slide. Replace with your own opening sentence here.</text>
    <text class="t-body" x="30" y="60">Keep it brief so the visual can carry the message.</text>
    <circle cx="95" cy="96" r="28" fill="var(--orange)"/>
    <circle cx="58" cy="128" r="28" fill="var(--sky)"/>
    <circle cx="132" cy="128" r="28" fill="var(--lgray)"/>
    <circle cx="95" cy="160" r="28" fill="var(--yellow)"/>
    <circle cx="95" cy="128" r="20" fill="#fff"/>
    <text class="t-label" x="95" y="126" text-anchor="middle">Rivalry or</text>
    <text class="t-label" x="95" y="133" text-anchor="middle">Competition</text>
    <g class="glyph"><rect x="90" y="84" width="10" height="7"/><circle cx="48" cy="128" r="4"/><rect x="137" y="123" width="9" height="9"/><path d="M90 172 h10 M95 166 v6"/></g>
    <circle cx="210" cy="100" r="14" fill="var(--blue)"/><path class="glyph" d="M204 104 l5-5 3 3 5-6"/>
    <text class="t-label" x="240" y="92">Your Title Here</text>
    <text class="t-cap" x="240" y="99">Short note on this item here.</text>
    <circle cx="198" cy="131" r="2.5" fill="var(--orange)"/><text class="t-cap" x="204" y="130">Your Title</text><text class="t-cap" x="204" y="135" fill="#f0b27a">Short note on item</text>
    <circle cx="280" cy="131" r="2.5" fill="var(--gray)"/><text class="t-cap" x="286" y="130">Your Title</text><text class="t-cap" x="286" y="135" fill="#f0b27a">Short note on item</text>
    <circle cx="198" cy="167" r="2.5" fill="var(--yellow)"/><text class="t-cap" x="204" y="166">Your Title</text><text class="t-cap" x="204" y="171" fill="#f0b27a">Short note on item</text>
    <circle cx="280" cy="167" r="2.5" fill="var(--sky)"/><text class="t-cap" x="286" y="166">Your Title</text><text class="t-cap" x="286" y="171" fill="#f0b27a">Short note on item</text>
    <rect y="203" width="400" height="23" fill="var(--navy)"/>
    <text class="t-brand" x="14" y="218">Bright Towns Forum</text>
    <text class="t-foot" x="360" y="216" text-anchor="end">Bright Towns Forum | Copyright 2017</text>
    <circle cx="371" cy="214" r="5" fill="var(--title)"/><text class="t-num" x="371" y="215.3" text-anchor="middle">52</text>
  </svg>

  <!-- Slide 53: five-part ring -->
  <svg class="slide c3 r2" viewBox="0 0 400 226">
    <text class="t-title" x="200" y="20" text-anchor="middle">Your Slide Title</text>
    <g fill="var(--title)"><rect x="191" y="30" width="2" height="2"/><rect x="195" y="30" width="2" height="2"/><rect x="199" y="30" width="2" height="2"/><rect x="203" y="30" width="2" height="2"/><rect x="207" y="30" width="2" height="2"/></g>
    <text class="t-body" x="30" y="51">Short summary line for this slide. Replace with your own opening sentence here.</text>
    <text class="t-body" x="30" y="60">Keep it brief so the visual can carry the message.</text>
    <g>
      <path d="M100 124 L100 67 A57 57 0 0 1 154 106 Z" fill="var(--red)"/>
      <path d="M100 124 L154 106 A57 57 0 0 1 134 170 Z" fill="var(--gray)"/>
      <path d="M100 124 L134 170 A57 57 0 0 1 66 170 Z" fill="var(--yellow)"/>
      <path d="M100 124 L66 170 A57 57 0 0 1 46 106 Z" fill="var(--blue)"/>
      <path d="M100 124 L46 106 A57 57 0 0 1 100 67 Z" fill="var(--dark)"/>
      <polygon points="100,104 119,118 112,141 88,141 81,118" fill="#fff"/>
      <g class="glyph"><rect x="80" y="82" width="9" height="7"/><rect x="121" y="95" width="9" height="9"/><rect x="126" y="137" width="8" height="9"/><rect x="80" y="150" width="9" height="7"/><circle cx="60" cy="123" r="4"/></g>
      <rect x="95" y="117" width="10" height="10" fill="none" stroke="var(--green)" stroke-width="1"/>
    </g>
    <g>
      <g fill="var(--yellow)"><rect x="207" y="92" width="2" height="2"/><rect x="210" y="92" width="2" height="2"/><rect x="213" y="92" width="2" height="2"/><rect x="216" y="92" width="2" height="2"/><rect x="219" y="92" width="2" height="2"/></g>
      <text class="t-label" x="240" y="87">Your Title - 01</text><text class="t-cap" x="240" y="94">Short note for this item.</text>
      <g fill="var(--gray)"><rect x="207" y="118" width="2" height="2"/><rect x="210" y="118" width="2" height="2"/><rect x="213" y="118" width="2" height="2"/><rect x="216" y="118" width="2" height="2"/><rect x="219" y="118" width="2" height="2"/></g>
      <text class="t-label" x="240" y="113">Your Title - 02</text><text class="t-cap" x="240" y="120">Short note for this item.</text>
      <g fill="var(--blue)"><rect x="207" y="144" width="2" height="2"/><rect x="210" y="144" width="2" height="2"/><rect x="213" y="144" width="2" height="2"/><rect x="216" y="144" width="2" height="2"/><rect x="219" y="144" width="2" height="2"/></g>
      <text class="t-label" x="240" y="139">Your Title - 03</text><text class="t-cap" x="240" y="146">Short note for this item.</text>
      <g fill="var(--green)"><rect x="207" y="170" width="2" height="2"/><rect x="210" y="170" width="2" height="2"/><rect x="213" y="170" width="2" height="2"/><rect x="216" y="170" width="2" height="2"/><rect x="219" y="170" width="2" height="2"/></g>
      <text class="t-label" x="240" y="165">Your Title - 04</text><text class="t-cap" x="240" y="172">Short note for this item.</text>
    </g>
    <rect y="203" width="400" height="23" fill="var(--navy)"/>
    <text class="t-brand" x="14" y="218">Bright Towns Forum</text>
    <text class="t-foot" x="360" y="216" text-anchor="end">Bright Towns Forum | Copyright 2017</text>
    <circle cx="371" cy="214" r="5" fill="var(--title)"/><text class="t-num" x="371" y="215.3" text-anchor="middle">53</text>
  </svg>

  <!-- Slide 54: linked cycle arrows -->
  <svg class="slide c1 r3" viewBox="0 0 400 226">
    <text class="t-title" x="200" y="20" text-anchor="middle">Your Slide Title</text>
    <g fill="var(--title)"><rect x="191" y="30" width="2" height="2"/><rect x="195" y="30" width="2" height="2"/><rect x="199" y="30" width="2" height="2"/><rect x="203" y="30" width="2" height="2"/><rect x="207" y="30" width="2" height="2"/></g>
    <text class="t-body" x="30" y="51">Short summary line for this slide. Replace with your own opening sentence here.</text>
    <text class="t-body" x="30" y="60">Keep it brief so the visual can carry the message.</text>
    <g fill="none" stroke-width="9">
      <circle cx="65" cy="114" r="30" stroke="var(--dark)"/>
      <circle cx="129" cy="114" r="30" stroke="var(--orange)"/>
      <circle cx="193" cy="114" r="30" stroke="var(--gray)"/>
      <circle cx="257" cy="114" r="30" stroke="var(--orange)"/>
      <circle cx="321" cy="114" r="30" stroke="var(--sky)"/>
    </g>
    <g>
      <polygon points="28,108 42,108 35,120" fill="var(--dark)"/>
      <polygon points="92,108 106,108 99,120" fill="var(--orange)"/>
      <polygon points="156,120 170,120 163,108" fill="var(--gray)"/>
      <polygon points="220,120 234,120 227,108" fill="var(--orange)"/>
      <polygon points="348,108 362,108 355,120" fill="var(--sky)"/>
    </g>
    <g fill="none" stroke-width="1.3">
      <rect x="59" y="108" width="12" height="12" stroke="var(--dark)"/>
      <path d="M123 120 l6-12 6 12z" stroke="var(--orange)"/>
      <path d="M187 120 l12-12" stroke="var(--gray)"/>
      <circle cx="257" cy="114" r="5" stroke="var(--orange)"/>
      <rect x="315" y="108" width="12" height="12" stroke="var(--sky)"/>
    </g>
    <g text-anchor="middle">
      <text class="t-label" x="65" y="162">Your Title</text><text class="t-cap" x="65" y="168">Short note for this item.</text>
      <text class="t-label" x="129" y="176">Your Title</text><text class="t-cap" x="129" y="182">Short note for this item.</text>
      <text class="t-label" x="193" y="162">Your Title</text><text class="t-cap" x="193" y="168">Short note for this item.</text>
      <text class="t-label" x="257" y="176">Your Title</text><text class="t-cap" x="257" y="182">Short note for this item.</text>
      <text class="t-label" x="321" y="162">Your Title</text><text class="t-cap" x="321" y="168">Short note for this item.</text>
    </g>
    <rect y="203" width="400" height="23" fill="var(--navy)"/>
    <text class="t-brand" x="14" y="218">Bright Towns Forum</text>
    <text class="t-foot" x="360" y="216" text-anchor="end">Bright Towns Forum | Copyright 2017</text>
    <circle cx="371" cy="214" r="5" fill="var(--title)"/><text class="t-num" x="371" y="215.3" text-anchor="middle">54</text>
  </svg>

  <!-- Slide 55: alternating half rings -->
  <svg class="slide c2 r3" viewBox="0 0 400 226">
    <text class="t-title" x="200" y="20" text-anchor="middle">Your Slide Title</text>
    <g fill="var(--title)"><rect x="191" y="30" width="2" height="2"/><rect x="195" y="30" width="2" height="2"/><rect x="199" y="30" width="2" height="2"/><rect x="203" y="30" width="2" height="2"/><rect x="207" y="30" width="2" height="2"/></g>
    <text class="t-body" x="30" y="51">Short summary line for this slide. Replace with your own opening sentence here.</text>
    <text class="t-body" x="30" y="60">Keep it brief so the visual can carry the message.</text>
    <g fill="none" stroke-width="9" stroke="#e3e3e3">
      <circle cx="62" cy="132" r="26"/><circle cx="116" cy="132" r="26"/><circle cx="170" cy="132" r="26"/>
      <circle cx="224" cy="132" r="26"/><circle cx="278" cy="132" r="26"/><circle cx="332" cy="132" r="26"/>
    </g>
    <g fill="none" stroke-width="9">
      <path d="M36 132 A26 26 0 0 1 88 132" stroke="var(--blue)"/>
      <path d="M90 132 A26 26 0 0 0 142 132" stroke="var(--orange)"/>
      <path d="M144 132 A26 26 0 0 1 196 132" stroke="var(--gray)"/>
      <path d="M198 132 A26 26 0 0 0 250 132" stroke="var(--yellow)"/>
      <path d="M252 132 A26 26 0 0 1 304 132" stroke="var(--blue)"/>
      <path d="M306 132 A26 26 0 0 0 358 132" stroke="var(--green)"/>
    </g>
    <g fill="none" stroke-width="1.3">
      <circle cx="62" cy="132" r="5" stroke="var(--blue)"/>
      <circle cx="116" cy="130" r="4" stroke="var(--orange)"/>
      <path d="M164 137 v-4 M170 137 v-8 M176 137 v-6" stroke="var(--gray)"/>
      <circle cx="224" cy="132" r="4" stroke="var(--yellow)"/>
      <circle cx="278" cy="132" r="4" stroke="var(--blue)"/>
      <path d="M327 137 l10-10" stroke="var(--green)"/>
    </g>
    <g text-anchor="middle">
      <text class="t-label" x="84" y="92">Your Title - 01</text><text class="t-cap" x="84" y="98">Short note for this item.</text>
      <text class="t-label" x="197" y="92">Your Title - 01</text><text class="t-cap" x="197" y="98">Short note for this item.</text>
      <text class="t-label" x="305" y="92">Your Title - 01</text><text class="t-cap" x="305" y="98">Short note for this item.</text>
      <text class="t-label" x="116" y="180">Your Title - 01</text><text class="t-cap" x="116" y="186">Short note for this item.</text>
      <text class="t-label" x="224" y="180">Your Title - 01</text><text class="t-cap" x="224" y="186">Short note for this item.</text>
      <text class="t-label" x="332" y="180">Your Title - 01</text><text class="t-cap" x="332" y="186">Short note for this item.</text>
    </g>
    <rect y="203" width="400" height="23" fill="var(--navy)"/>
    <text class="t-brand" x="14" y="218">Bright Towns Forum</text>
    <text class="t-foot" x="360" y="216" text-anchor="end">Bright Towns Forum | Copyright 2017</text>
    <circle cx="371" cy="214" r="5" fill="var(--title)"/><text class="t-num" x="371" y="215.3" text-anchor="middle">55</text>
  </svg>

  <!-- Slide 56: growth-share matrix -->
  <svg class="slide c3 r3" viewBox="0 0 400 226">
    <text class="t-title" x="200" y="20" text-anchor="middle">Your Slide Title</text>
    <g fill="var(--title)"><rect x="191" y="30" width="2" height="2"/><rect x="195" y="30" width="2" height="2"/><rect x="199" y="30" width="2" height="2"/><rect x="203" y="30" width="2" height="2"/><rect x="207" y="30" width="2" height="2"/></g>
    <text class="t-body" x="30" y="51">Short summary line for this slide. Replace with your own opening sentence here.</text>
    <text class="t-body" x="30" y="60">Keep it brief so the visual can carry the message.</text>
    <text class="t-cap" x="115" y="74" text-anchor="middle">Market Share</text>
    <text class="t-cap" x="60" y="82">High</text><text class="t-cap" x="170" y="82" text-anchor="end">Low</text>
    <line x1="66" y1="79" x2="164" y2="79" stroke="#bbb" stroke-width=".4"/>
    <line x1="62" y1="86" x2="62" y2="186" stroke="#bbb" stroke-width=".4"/>
    <text class="t-cap" x="56" y="130" transform="rotate(-90 56 130)" text-anchor="middle">Market Growth</text>
    <text class="t-cap" x="60" y="192">Low</text>
    <rect x="68" y="84" width="53" height="52" rx="4" fill="var(--red)"/>
    <rect x="124" y="84" width="53" height="52" rx="4" fill="var(--dark)"/>
    <rect x="68" y="140" width="53" height="52" rx="4" fill="var(--gray)"/>
    <rect x="124" y="140" width="53" height="52" rx="4" fill="var(--orange)"/>
    <g class="glyph"><rect x="89" y="102" width="10" height="12"/><rect x="145" y="102" width="10" height="12"/><rect x="89" y="158" width="10" height="12"/><rect x="145" y="158" width="10" height="12"/></g>
    <g text-anchor="middle">
      <text class="t-in" x="94.5" y="126">STARS</text><text class="t-in" x="150.5" y="126">QUESTION</text>
      <text class="t-in" x="94.5" y="182">CASH</text><text class="t-in" x="150.5" y="182">CONVERT</text>
    </g>
    <g>
      <g fill="var(--red)"><rect x="220" y="86" width="2" height="2"/><rect x="223" y="86" width="2" height="2"/><rect x="226" y="86" width="2" height="2"/><rect x="229" y="86" width="2" height="2"/><rect x="232" y="86" width="2" height="2"/></g>
      <text class="t-label" x="252" y="80">Your Title - 01</text><text class="t-cap" x="252" y="87">Short note for this item.</text>
      <g fill="var(--dark)"><rect x="220" y="112" width="2" height="2"/><rect x="223" y="112" width="2" height="2"/><rect x="226" y="112" width="2" height="2"/><rect x="229" y="112" width="2" height="2"/><rect x="232" y="112" width="2" height="2"/></g>
      <text class="t-label" x="252" y="106">Your Title - 02</text><text class="t-cap" x="252" y="113">Short note for this item.</text>
      <g fill="var(--gray)"><rect x="220" y="138" width="2" height="2"/><rect x="223" y="138" width="2" height="2"/><rect x="226" y="138" width="2" height="2"/><rect x="229" y="138" width="2" height="2"/><rect x="232" y="138" width="2" height="2"/></g>
      <text class="t-label" x="252" y="132">Your Title - 03</text><text class="t-cap" x="252" y="139">Short note for this item.</text>
      <g fill="var(--orange)"><rect x="220" y="164" width="2" height="2"/><rect x="223" y="164" width="2" height="2"/><rect x="226" y="164" width="2" height="2"/><rect x="229" y="164" width="2" height="2"/><rect x="232" y="164" width="2" height="2"/></g>
      <text class="t-label" x="252" y="158">Your Title - 04</text><text class="t-cap" x="252" y="165">Short note for this item.</text>
    </g>
    <rect y="203" width="400" height="23" fill="var(--navy)"/>
    <text class="t-brand" x="14" y="218">Bright Towns Forum</text>
    <text class="t-foot" x="360" y="216" text-anchor="end">Bright Towns Forum | Copyright 2017</text>
    <circle cx="371" cy="214" r="5" fill="var(--title)"/><text class="t-num" x="371" y="215.3" text-anchor="middle">56</text>
  </svg>
</div>
</body>
</html>
```